Fire Risk Assessment App needs a sleek UI design

I need a sleek, modern but professional design for my 5 page Fire Risk Assessment App. Include gradient background, fire themed colours including reds, yellows, light orange and a touch of black. Design must ooze simplicity and professionalism. This is for the UK market. See attached images and word doc for more information.

Target Market(s)

General public and business owners

Industry/Entity Type

Technology / Fire Safety

Colors
00AB8E
00BBA5
67D7C9
C6EFE9
E9F9F6
59FF00
82FF00
B8FF75
E3FFCB
F4FFEA
FFC000
F8CF3A
FAE287
FDF2CF
FEFAEE
F0912C
F2A743
F7CA91
FBE8D2
FDF5EE
EE7325
F08F49
F5BC92
FAE3D3
FDF4ED
EB3D1F
EC4F4E
F09395
F8D3D4
FCEDEE

```html
<!DOCTYPE html>
<html lang="en">
<head>
<meta charset="utf-8">
<title>Fire Risk Assessment App – Screens</title>
<link href="https://fonts.googleapis.com/css2?family=Montserrat:wght@400;500;600;700&display=swap" rel="stylesheet">
<style>
  :root{
    --stage:#dcdcdc;
    --ink:#1b1b1b;
    --bar:#3c3c3c;
    --white:#ffffff;
    --warm-top:#ffc84a;
    --warm-mid:#ffaf45;
    --warm-low:#ff9252;
    --red:#eb3d1f;
    --red-soft:#ec4f4e;
    --green:#3fb54a;
    --amber:#ffc000;
    --orange:#f0912c;
    --chat:#f6962c;
  }
  *{box-sizing:border-box;margin:0;padding:0}
  html,body{width:1200px;height:848px;overflow:hidden}
  body{background:var(--stage);font-family:"Montserrat",sans-serif;color:var(--ink);position:relative}

  .screen{position:absolute;top:46px;width:349px;height:755px;overflow:hidden;
    background:
      radial-gradient(circle at 78% 58%, rgba(255,140,70,.35) 0, rgba(255,140,70,0) 38%),
      radial-gradient(circle at 20% 30%, rgba(255,230,120,.35) 0, rgba(255,230,120,0) 40%),
      linear-gradient(180deg,var(--warm-top) 0%,var(--warm-mid) 50%,var(--warm-low) 100%);}
  .screen--welcome{left:42px}
  .screen--dashboard{left:426px}
  .screen--support{left:809px}

  .abs{position:absolute}
  .center-x{left:0;right:0;text-align:center}

  /* header */
  .topbar{position:absolute;top:0;left:0;right:0;height:49px;background:var(--bar);display:flex;align-items:center;justify-content:center;gap:10px;color:var(--white);font-weight:700;font-size:17px}

  /* welcome */
  .headline{top:14px;font-weight:700;font-size:17px;line-height:22px}
  .doc-art{left:55px;top:74px;width:216px;height:293px;border-radius:4px;
    background:linear-gradient(160deg,#ffffff 0%,#f6f1ea 60%,#e7573f 100%);transform:rotate(6deg);box-shadow:0 4px 10px rgba(0,0,0,.15)}
  .search{left:21px;top:388px;width:307px;height:34px;border:1.5px solid #6b3b12;border-radius:10px;display:flex;align-items:center;justify-content:space-between;padding:0 8px;font-size:13px}
  .btn{position:absolute;left:74px;width:201px;height:46px;background:var(--white);display:flex;align-items:center;justify-content:center;gap:14px;font-size:12px;font-weight:500}
  .btn--create{top:445px}
  .btn--login{top:548px}
  .lead{font-size:15px;line-height:22px}
  .lead--any{top:503px}
  .lead--endorse{top:607px}
  .fingerprint{left:143px;top:665px}

  /* dashboard */
  .action{position:absolute;text-align:center;font-size:13px;font-weight:500}
  .action__icon{width:60px;height:60px;border-radius:50%;background:var(--white);display:flex;align-items:center;justify-content:center;margin:0 auto 6px}
  .action--fra{left:104px;top:80px;width:140px}
  .action--fra .action__icon{background:var(--red)}
  .action--commercial{left:49px;top:177px;width:100px}
  .action--residential{left:204px;top:177px;width:100px}

  .section{position:absolute;left:20px;width:189px;height:34px;border:1px solid #5b3a15;display:flex;align-items:center;justify-content:space-between;padding:0 10px;font-size:14px;font-weight:500}
  .section--done{top:287px}
  .section--progress{top:415px}
  .section--purchases{top:549px}

  .site{position:absolute;left:20px;top:334px;display:flex;align-items:center;gap:9px;font-size:13px;font-weight:600}
  .site__badge{width:46px;height:46px;border-radius:50%;background:var(--white);display:flex;align-items:center;justify-content:center}

  .list-item{position:absolute;left:20px;display:flex;align-items:center;gap:11px;font-size:13px;font-weight:500}
  .list-item::before{content:"";width:18px;height:18px;border:1.6px solid var(--ink);border-radius:50%}

  .tabbar{position:absolute;left:0;right:0;bottom:0;height:47px;background:var(--white);display:flex;align-items:center}
  .tabbar__item{flex:1;display:flex;align-items:center;justify-content:center;height:32px;border-right:1px solid #333}
  .tabbar__item:last-child{border-right:0}

  /* support */
  .prompt{left:20px;top:84px;font-size:16px;font-weight:500}
  .prompt-mic{left:311px;top:84px}
  .reply{left:21px;top:115px;width:307px;height:103px;border:1.5px solid #5b3a15;border-radius:8px}
  .send{left:220px;top:238px;width:108px;height:40px;background:var(--white);display:flex;align-items:center;justify-content:center;gap:16px;font-size:13px;font-weight:500}
</style>
</head>
<body>

<!-- Welcome screen -->
<section class="screen screen--welcome">
  <h1 class="abs center-x headline">The most user friendly'<br>Fire Risk Assessment App available.</h1>
  <div class="abs doc-art" role="img" aria-label="Illustration of stacked fire risk assessment sheets with an electrical hazard question and a photo of red fire extinguishers"></div>

  <div class="abs search">
    <span>Lorem i |</span>
    <svg width="20" height="22" viewBox="0 0 20 22" fill="none" stroke="#1b1b1b" stroke-width="1.6"><rect x="7" y="2" width="6" height="11" rx="3"/><path d="M4 10a6 6 0 0 0 12 0M10 16v4M7 20h6"/></svg>
  </div>

  <div class="btn btn--create">
    <svg width="26" height="26" viewBox="0 0 26 26"><circle cx="10" cy="7" r="5" fill="#1b1b1b"/><path d="M1 24c0-6 4-10 9-10s7 2 8 4v6z" fill="#1b1b1b"/><circle cx="20" cy="20" r="5" fill="#1b1b1b"/><path d="M20 17v6M17 20h6" stroke="#fff" stroke-width="1.6"/></svg>
    <span>Create a Free account</span>
  </div>
  <p class="abs center-x lead lead--any">Any Responsible Person can do it.</p>

  <div class="btn btn--login">
    <svg width="32" height="28" viewBox="0 0 32 28"><circle cx="11" cy="7" r="6" fill="#1b1b1b"/><path d="M0 27c0-7 5-12 11-12s9 3 10 5v7z" fill="#1b1b1b"/><rect x="20" y="17" width="11" height="10" rx="1" fill="#1b1b1b"/><path d="M22 17v-3a3.5 3.5 0 0 1 7 0v3" fill="none" stroke="#1b1b1b" stroke-width="1.8"/></svg>
    <span>Customer Log In</span>
  </div>
  <p class="abs center-x lead lead--endorse">Created and endorsed by<br>British Firefighters.</p>

  <svg class="abs fingerprint" width="62" height="76" viewBox="0 0 62 76" fill="none" stroke="#111" stroke-width="3" stroke-linecap="round">
    <path d="M8 20a28 28 0 0 1 46 0"/>
    <path d="M4 40c0-16 12-28 27-28s27 12 27 28v6"/>
    <path d="M10 54c0-4 0-10 0-14 0-12 9-21 21-21s21 9 21 21v12c0 6-1 12-3 16"/>
    <path d="M17 64c0-8 0-16 0-24 0-8 6-14 14-14s14 6 14 14v10c0 8-2 16-6 22"/>
    <path d="M24 70c0-10 0-20 0-30a7 7 0 0 1 14 0v12c0 8-2 14-5 20"/>
    <path d="M31 40v14c0 6-1 12-4 18"/>
  </svg>
</section>

<!-- Dashboard screen -->
<section class="screen screen--dashboard">
  <header class="topbar">
    <svg width="44" height="26" viewBox="0 0 44 26"><path d="M2 24a20 20 0 0 1 40 0z" fill="#fff"/><path d="M5 24a17 17 0 0 1 6-13l4 5a11 11 0 0 0-4 8z" fill="#ec4f4e"/><path d="M11 11a17 17 0 0 1 11-4v6a11 11 0 0 0-7 3z" fill="#f0912c"/><path d="M22 7a17 17 0 0 1 11 4l-4 5a11 11 0 0 0-7-3z" fill="#ffc000"/><path d="M33 11a17 17 0 0 1 6 13h-6a11 11 0 0 0-4-8z" fill="#3fb54a"/><path d="M22 24l9-9" stroke="#1b1b1b" stroke-width="2.4"/><circle cx="22" cy="24" r="2.5" fill="#1b1b1b"/></svg>
    <span>Dashboard</span>
  </header>

  <div class="action action--fra">
    <div class="action__icon">
      <svg width="34" height="34" viewBox="0 0 34 34"><path d="M12 3h10v9h9v10h-9v9H12v-9H3V12h9z" fill="#fff"/></svg>
    </div>
    <span>Fire Risk Assessment</span>
  </div>

  <div class="action action--commercial">
    <div class="action__icon">
      <svg width="38" height="34" viewBox="0 0 38 34" fill="#1b1b1b"><path d="M8 6h22v4h4v24H4V10h4z"/><g fill="#fff"><rect x="9" y="12" width="3" height="4"/><rect x="14" y="12" width="3" height="4"/><rect x="21" y="12" width="3" height="4"/><rect x="26" y="12" width="3" height="4"/><rect x="9" y="19" width="3" height="4"/><rect x="14" y="19" width="3" height="4"/><rect x="21" y="19" width="3" height="4"/><rect x="26" y="19" width="3" height="4"/><rect x="16" y="26" width="6" height="8"/></g><rect x="17" y="0" width="4" height="6"/></svg>
    </div>
    <span>Commercial</span>
  </div>

  <div class="action action--residential">
    <div class="action__icon">
      <svg width="38" height="34" viewBox="0 0 38 34" fill="#1b1b1b"><path d="M19 1L1 15h5v18h26V15h5z"/><path d="M19 6L9 14v1h20v-1z" fill="#fff"/><circle cx="19" cy="11" r="2"/><g fill="#fff"><rect x="10" y="18" width="3" height="12"/><rect x="16" y="18" width="3" height="12"/><rect x="22" y="18" width="3" height="12"/></g></svg>
    </div>
    <span>Residential</span>
  </div>

  <div class="section section--done">
    <span>Completed</span>
    <svg width="24" height="22" viewBox="0 0 24 22"><circle cx="11" cy="12" r="9" fill="#3fb54a"/><path d="M5 12l5 5L22 3" fill="none" stroke="#1b1b1b" stroke-width="2.6"/></svg>
  </div>

  <div class="site">
    <div class="site__badge">
      <svg width="30" height="26" viewBox="0 0 38 34" fill="#1b1b1b"><path d="M8 6h22v4h4v24H4V10h4z"/><g fill="#fff"><rect x="9" y="12" width="3" height="4"/><rect x="14" y="12" width="3" height="4"/><rect x="21" y="12" width="3" height="4"/><rect x="26" y="12" width="3" height="4"/><rect x="9" y="19" width="3" height="4"/><rect x="14" y="19" width="3" height="4"/><rect x="21" y="19" width="3" height="4"/><rect x="26" y="19" width="3" height="4"/><rect x="16" y="26" width="6" height="8"/></g></svg>
    </div>
    <span>Milo's Barbershop</span>
  </div>

  <div class="section section--progress">
    <span>In Progress</span>
    <svg width="20" height="20" viewBox="0 0 20 20"><circle cx="10" cy="10" r="9" fill="#1b1b1b"/><path d="M10 10V1a9 9 0 0 1 9 9z" fill="#fff"/><path d="M10 10H1" stroke="#fff" stroke-width="1.4"/></svg>
  </div>
  <div class="list-item" style="top:469px">Heron Rd School</div>
  <div class="list-item" style="top:497px">Elm Grove Nursing Home</div>

  <div class="section section--purchases">
    <span>Purchases</span>
    <svg width="20" height="20" viewBox="0 0 20 20"><circle cx="10" cy="10" r="9" fill="#1b1b1b"/><path d="M10 10V1a9 9 0 0 1 9 9z" fill="#fff"/><path d="M10 10H1" stroke="#fff" stroke-width="1.4"/></svg>
  </div>
  <div class="list-item" style="top:603px">Residential Fire Risk Assessment</div>
  <div class="list-item" style="top:631px">Commercial Fire Risk Assessment</div>
  <div class="list-item" style="top:659px">Commercial Fire Risk Assessment</div>

  <nav class="tabbar">
    <div class="tabbar__item"><svg width="44" height="26" viewBox="0 0 44 26"><path d="M5 24a17 17 0 0 1 6-13l4 5a11 11 0 0 0-4 8z" fill="#ec4f4e"/><path d="M11 11a17 17 0 0 1 11-4v6a11 11 0 0 0-7 3z" fill="#f0912c"/><path d="M22 7a17 17 0 0 1 11 4l-4 5a11 11 0 0 0-7-3z" fill="#ffc000"/><path d="M33 11a17 17 0 0 1 6 13h-6a11 11 0 0 0-4-8z" fill="#3fb54a"/><path d="M22 24l9-9" stroke="#1b1b1b" stroke-width="2.4"/><circle cx="22" cy="24" r="2.5" fill="#1b1b1b"/></svg></div>
    <div class="tabbar__item"><svg width="34" height="28" viewBox="0 0 34 28"><path d="M10 8l14-6 2 5z" fill="#1b1b1b"/><rect x="1" y="8" width="32" height="19" rx="2" fill="#1b1b1b"/><g fill="#fff"><rect x="5" y="13" width="8" height="4"/><rect x="5" y="21" width="4" height="2"/><rect x="11" y="21" width="4" height="2"/><rect x="17" y="21" width="4" height="2"/><rect x="23" y="21" width="4" height="2"/></g></svg></div>
    <div class="tabbar__item"><svg width="34" height="30" viewBox="0 0 34 30"><path d="M4 1h26a3 3 0 0 1 3 3v15a3 3 0 0 1-3 3H15l-7 7v-7H4a3 3 0 0 1-3-3V4a3 3 0 0 1 3-3z" fill="#1b1b1b"/><circle cx="11" cy="11" r="1.8" fill="#fff"/><circle cx="17" cy="11" r="1.8" fill="#fff"/><circle cx="23" cy="11" r="1.8" fill="#fff"/></svg></div>
    <div class="tabbar__item"><svg width="36" height="32" viewBox="0 0 36 32" fill="#1b1b1b"><rect x="20" y="2" width="14" height="29" fill="none" stroke="#1b1b1b" stroke-width="2"/><circle cx="26" cy="8" r="2.6"/><path d="M25 11l-4 5 3 2 2-3 1 6-3 6h3l3-5 1 5h3l-2-8v-6z"/><path d="M6 20c3 2 5 5 5 8a5 5 0 0 1-10 0c0-2 1-4 2-5 0 2 1 3 2 3-1-3 0-5 1-6z"/></svg></div>
  </nav>
</section>

<!-- Support screen -->
<section class="screen screen--support">
  <header class="topbar">
    <svg width="30" height="28" viewBox="0 0 34 30"><path d="M4 1h26a3 3 0 0 1 3 3v15a3 3 0 0 1-3 3H15l-7 7v-7H4a3 3 0 0 1-3-3V4a3 3 0 0 1 3-3z" fill="var(--chat)"/><circle cx="11" cy="11" r="1.8" fill="#fff"/><circle cx="17" cy="11" r="1.8" fill="#fff"/><circle cx="23" cy="11" r="1.8" fill="#fff"/></svg>
    <span>Support</span>
  </header>

  <p class="abs prompt">Type / Record Your Response Here</p>
  <svg class="abs prompt-mic" width="20" height="22" viewBox="0 0 20 22" fill="none" stroke="#1b1b1b" stroke-width="1.6"><rect x="7" y="2" width="6" height="11" rx="3"/><path d="M4 10a6 6 0 0 0 12 0M10 16v4M7 20h6"/></svg>
  <div class="abs reply"></div>

  <div class="abs send">
    <svg width="34" height="30" viewBox="0 0 34 30"><path d="M33 1L1 13l10 4 3 12 5-8 8 5z" fill="#1b1b1b"/><path d="M11 17L33 1 15 20" fill="none" stroke="#fff" stroke-width="1.4"/></svg>
    <span>Send</span>
  </div>

  <nav class="tabbar">
    <div class="tabbar__item"><svg width="50" height="28" viewBox="0 0 50 28"><path d="M2 26a23 23 0 0 1 46 0h-8a15 15 0 0 0-30 0z" fill="#1b1b1b"/><path d="M25 26l10-9" stroke="#1b1b1b" stroke-width="3"/><circle cx="25" cy="26" r="2.5" fill="#1b1b1b"/></svg></div>
    <div class="tabbar__item"><svg width="34" height="28" viewBox="0 0 34 28"><path d="M10 8l14-6 2 5z" fill="#1b1b1b"/><rect x="1" y="8" width="32" height="19" rx="2" fill="#1b1b1b"/><g fill="#fff"><rect x="5" y="13" width="8" height="4"/><rect x="5" y="21" width="4" height="2"/><rect x="11" y="21" width="4" height="2"/><rect x="17" y="21" width="4" height="2"/><rect x="23" y="21" width="4" height="2"/></g></svg></div>
    <div class="tabbar__item"><svg width="34" height="30" viewBox="0 0 34 30"><path d="M4 1h26a3 3 0 0 1 3 3v15a3 3 0 0 1-3 3H15l-7 7v-7H4a3 3 0 0 1-3-3V4a3 3 0 0 1 3-3z" fill="var(--chat)"/><circle cx="11" cy="11" r="1.8" fill="#fff"/><circle cx="17" cy="11" r="1.8" fill="#fff"/><circle cx="23" cy="11" r="1.8" fill="#fff"/></svg></div>
    <div class="tabbar__item"><svg width="36" height="32" viewBox="0 0 36 32" fill="#1b1b1b"><rect x="20" y="2" width="14" height="29" fill="none" stroke="#1b1b1b" stroke-width="2"/><circle cx="26" cy="8" r="2.6"/><path d="M25 11l-4 5 3 2 2-3 1 6-3 6h3l3-5 1 5h3l-2-8v-6z"/><path d="M6 20c3 2 5 5 5 8a5 5 0 0 1-10 0c0-2 1-4 2-5 0 2 1 3 2 3-1-3 0-5 1-6z"/></svg></div>
  </nav>
</section>

</body>
</html>
```